Tech business card design

We need an amazing business card design for our new business 'Pexla' a marketing tech startup based in Sydney, Australia. We provide an online marketplace for businesses to search and buy advertising media, connect with service providers and learn more about marketing. We wish to communicate 'cool tech', reliability and professionalism and design based around our logo.

Target Market(s)

Business Owners

Contact Information for Business Card

Name
Position
Email Address
Website
Phone Number

Font styles to use
Other font styles liked:
• Avenir & Avenir Next

Colors

Designer to choose colors to be used in the design.

```html
<!DOCTYPE html>
<html lang="en">
<head>
<meta charset="utf-8">
<title>Pexla Business Card</title>
<link rel="stylesheet" href="https://fonts.googleapis.com/css2?family=Lato:wght@400;700;900&family=Nunito+Sans:wght@700;800&display=swap">
<style>
  :root {
    --backdrop: #8c8c8c;
    --card-white: #ffffff;
    --navy: #1b1d4a;
    --navy-deep: #12143d;
    --ink-grey: #555a60;
    --rule-grey: #9a9a9a;
  }
  * { margin: 0; padding: 0; box-sizing: border-box; }
  html, body {
    width: 1200px; height: 1200px; overflow: hidden;
    background: var(--backdrop);
  }
  .stage { position: relative; width: 1200px; height: 1200px; }
  .card {
    position: absolute; top: 310px; width: 364px; height: 594px;
    box-shadow: 3px 4px 8px rgba(0,0,0,0.35);
  }
  .card-front { left: 234px; background: var(--card-white); }
  .card-back {
    left: 627px; width: 370px;
    background: linear-gradient(180deg, #23254f 0%, var(--navy-deep) 100%);
  }
  .wordmark {
    position: absolute; left: 0; right: 0; text-align: center;
    font-family: "Lato", sans-serif; font-weight: 900;
    font-size: 88px; letter-spacing: 1px; line-height: 1;
  }
  .card-front .wordmark { top: 158px; color: var(--navy); }
  .card-back .wordmark { top: 252px; color: var(--card-white); }
  .contact-block {
    position: absolute; left: 0; right: 0; top: 378px; text-align: center;
  }
  .person-name {
    font-family: "Nunito Sans", sans-serif; font-weight: 800;
    font-size: 21px; letter-spacing: 1px; color: var(--navy);
    line-height: 26px;
  }
  .person-role {
    font-family: "Lato", sans-serif; font-size: 16px; color: var(--ink-grey);
    line-height: 20px;
  }
  .icon-row {
    display: flex; align-items: center; justify-content: center;
    margin-top: 14px; gap: 4px;
  }
  .icon-rule { width: 52px; height: 1px; background: var(--rule-grey); }
  .icon-row svg { display: block; }
  .icon-group { display: flex; gap: 3px; margin: 0 2px; }
  .contact-lines {
    margin-top: 11px;
    font-family: "Lato", sans-serif; font-size: 16px; line-height: 21.5px;
    color: var(--ink-grey);
  }
</style>
</head>
<body>
<main class="stage">
  <section class="card card-front">
    <div class="wordmark">Pexla</div>
    <div class="contact-block">
      <div class="person-name">MARCUS HALE</div>
      <div class="person-role">Managing Director</div>
      <div class="icon-row">
        <span class="icon-rule"></span>
        <span class="icon-group">
          <svg width="24" height="24" viewBox="0 0 24 24" aria-label="Phone">
            <circle cx="12" cy="12" r="12" fill="var(--navy)"/>
            <path d="M7 9.5c0-1.2 2.2-2.2 5-2.2s5 1 5 2.2v1h-2.4v-1.2h-5.2v1.2H7z" fill="#fff"/>
            <rect x="8.5" y="11.5" width="7" height="5" rx="1" fill="#fff"/>
          </svg>
          <svg width="24" height="24" viewBox="0 0 24 24" aria-label="Email">
            <circle cx="12" cy="12" r="12" fill="var(--navy)"/>
            <rect x="6.5" y="8" width="11" height="8" fill="none" stroke="#fff" stroke-width="1.3"/>
            <path d="M6.5 8l5.5 4.5L17.5 8" fill="none" stroke="#fff" stroke-width="1.3"/>
          </svg>
          <svg width="24" height="24" viewBox="0 0 24 24" aria-label="Website">
            <circle cx="12" cy="12" r="12" fill="var(--navy)"/>
            <circle cx="12" cy="12" r="6" fill="none" stroke="#fff" stroke-width="1.3"/>
            <ellipse cx="12" cy="12" rx="2.6" ry="6" fill="none" stroke="#fff" stroke-width="1.1"/>
            <line x1="6" y1="12" x2="18" y2="12" stroke="#fff" stroke-width="1.1"/>
          </svg>
        </span>
        <span class="icon-rule"></span>
      </div>
      <div class="contact-lines">
        <div class="contact-phone">044-987 612 345</div>
        <div class="contact-email">info@pexlamail.com</div>
        <div class="contact-web">www.pexlamedia.com</div>
      </div>
    </div>
  </section>
  <section class="card card-back">
    <div class="wordmark">Pexla</div>
  </section>
</main>
</body>
</html>
```